Interior Design/ New Construction interior finishes

Interior Design Website

Target Market(s)

Home builders, New Construction, Renovations, Public

Industry/Entity Type

Construction

Coding

Coded - Design and coding required

Number of Pages Required

1 page

Font styles to use
Sans Serif

Colors

Designer to choose colors to be used in the design.

Requirements
Must have
• Section to upload pictures of projects
• Simple and modern design
• Designer 1 details about myself
• Logo
• Upload section for photos for future jobs
Nice to have
• Sections they can click on to see certain rooms in a house
• Decorating, floral arrangements, holiday decorating.
• I have lots of before and after as well. Maybe a section for those.

```html
<!DOCTYPE html>
<html lang="en">
<head>
<meta charset="utf-8">
<title>Vela Interiors</title>
<link rel="stylesheet" href="https://fonts.googleapis.com/css2?family=Poppins:wght@300;400;500&family=Oswald:wght@400;500&display=swap">
<style>
:root{
  --accent:#f2541b;
  --ink:#1d1d1d;
  --text:#333;
  --dark:#121212;
  --dark-2:#2a2a2a;
  --light:#f1f1f1;
  --white:#fff;
  --wood:#7a5238;
  --cream:#d9cdbb;
}
*{box-sizing:border-box;margin:0;padding:0}
html,body{width:1200px;height:3141px;overflow:hidden}
body{position:relative;font-family:'Poppins',sans-serif;color:var(--text);background:var(--white)}
.abs{position:absolute}
.photo{position:absolute;display:block}

/* header + hero */
.hero{left:0;top:0;width:1200px;height:628px;background:linear-gradient(100deg,#6b4a33 0%,#b08a67 30%,#d8cbb7 55%,#9c7a5c 80%,#5a3f2c 100%)}
.header-bar{left:0;top:0;width:1200px;height:136px;background:rgba(10,10,10,.72)}
.brand{left:52px;top:26px;width:200px;text-align:center;color:var(--white);white-space:nowrap}
.brand .dot{display:block;width:56px;height:56px;border:3px solid var(--white);border-radius:50%;margin:0 auto 8px}
.brand span{font-size:19px;letter-spacing:2px}
.nav{left:410px;top:72px;display:flex;gap:0;align-items:center}
.nav a{color:var(--white);text-decoration:none;font-size:15px;letter-spacing:.5px;margin-right:58px;white-space:nowrap}
.nav a.cta{border:2px solid var(--white);color:var(--accent);padding:4px 14px;margin-right:0;margin-left:-6px}
.phone{left:968px;top:32px;color:var(--white);font-size:14px;display:flex;align-items:center;gap:8px}
.hero-box{left:333px;top:264px;width:534px;height:232px;background:rgba(15,15,15,.8);display:flex;align-items:center;padding-left:18px;color:var(--white)}
.hero-box .dot{flex:none;width:100px;height:100px;border:3px solid var(--white);border-radius:50%;margin-right:20px}
.hero-box .rule{flex:none;width:3px;height:84px;background:var(--white);margin-right:16px}
.hero-box h1{font-weight:400;font-size:40px;letter-spacing:4px;line-height:1;white-space:nowrap}
.hero-box p{font-size:15px;margin-top:10px;font-weight:300;white-space:nowrap}
.arrow{top:364px}

/* welcome */
.welcome{left:0;top:628px;width:1200px;height:381px;background:linear-gradient(180deg,#ececec,#f6f6f6 60%,#e8e8e8);text-align:center}
.welcome h2{position:absolute;top:80px;width:100%;font-weight:400;font-size:35px;letter-spacing:2.5px;color:var(--ink)}
.welcome p{position:absolute;left:224px;top:141px;width:752px;font-size:13.5px;line-height:23px;color:#222}
.btn{position:absolute;display:flex;align-items:center;justify-content:center;font-size:13px;text-decoration:none;white-space:nowrap}
.btn.solid{background:var(--accent);color:var(--white)}
.btn.line{border:2px solid var(--accent);color:var(--accent);background:rgba(255,255,255,.6)}

/* split sections */
.split{left:0;width:1200px;height:480px;background:var(--white)}
.split .side{position:absolute;left:758px;top:0;width:442px;height:480px;background:linear-gradient(160deg,#2b2420,#0f0d0c 60%,#1b1714)}
.card{position:absolute;overflow:hidden}
.card .label{position:absolute;left:0;bottom:0;width:100%;padding:0 0 16px 36px;color:var(--white);font-size:23px;letter-spacing:1px;background:linear-gradient(0deg,rgba(0,0,0,.65),rgba(0,0,0,0));height:90px;display:flex;align-items:flex-end;white-space:nowrap}
.feature .card .label{padding-left:28px;font-size:22px}
.vtitle{position:absolute;writing-mode:vertical-rl;font-family:'Oswald',sans-serif;font-weight:500;font-size:44px;letter-spacing:4px;color:var(--white);white-space:nowrap}
.feature{left:0;top:1489px;width:1200px;height:517px;background:linear-gradient(120deg,#3a3e45,#22252a 50%,#33302c)}
.feature .card{border:2px solid rgba(255,255,255,.75)}

/* touch */
.touch{left:0;top:2486px;width:1200px;height:310px;background:linear-gradient(180deg,#2a2622,#141210 60%,#2b241e)}
.touch h2{position:absolute;top:88px;width:100%;text-align:center;font-family:'Oswald',sans-serif;font-weight:500;font-size:46px;color:var(--white);letter-spacing:1px}
.touch .field{left:310px;top:159px;width:412px;height:48px;background:var(--white);font-size:12px;font-style:italic;color:#888;display:flex;align-items:center;padding-left:22px}
.touch .send{left:729px;top:159px;width:161px;height:48px;background:var(--accent);color:var(--white);font-weight:500;font-size:17px;display:flex;align-items:center;justify-content:center}

/* footer */
.footer{left:0;top:2796px;width:1200px;height:345px;background:var(--light);color:#222}
.footer .brand{left:45px;top:52px;width:320px;color:#111}
.footer .brand .dot{width:100px;height:100px;border-color:#111}
.footer .brand span{font-size:28px;letter-spacing:3px}
.socials{left:112px;top:214px;display:flex;gap:9px}
.socials i{width:30px;height:30px;border-radius:50%;background:var(--accent);display:block}
.col h4{font-weight:400;font-size:18px;margin-bottom:20px}
.contact li{list-style:none;display:flex;gap:18px;font-size:14px;line-height:23px;margin-bottom:13px;white-space:nowrap}
.contact svg{flex:none;margin-top:4px}
.links li{list-style:none;font-size:13px;line-height:19px;padding-left:26px;position:relative;white-space:nowrap}
.links li::before{content:'›';position:absolute;left:0;top:-1px}
.footer .rule{left:86px;top:272px;width:1028px;height:1px;background:#cfcfcf}
.footer .copy{top:300px;width:100%;text-align:center;font-size:14px;letter-spacing:1px}
</style>
</head>
<body>

<section class="hero abs" role="img" aria-label="Photo of a bright open-plan kitchen and dining room with wooden floors"></section>
<header class="header-bar abs"></header>
<div class="brand abs"><span class="dot"></span><span>Vela Interiors</span></div>
<nav class="nav abs">
  <a href="#">Home</a><a href="#">What We Do</a><a href="#">Who We Are</a><a href="#">Our Works</a><a href="#">Blog</a><a href="#" class="cta">Contact Us</a>
</nav>
<div class="phone abs">
  <svg width="12" height="12" viewBox="0 0 24 24"><path fill="#f2541b" d="M6.6 10.8a15 15 0 0 0 6.6 6.6l2.2-2.2c.3-.3.7-.4 1-.2 1.1.4 2.3.6 3.6.6.6 0 1 .4 1 1V20c0 .6-.4 1-1 1A17 17 0 0 1 3 4c0-.6.4-1 1-1h3.5c.6 0 1 .4 1 1 0 1.3.2 2.5.6 3.6.1.3 0 .7-.2 1z"/></svg>
  +0100 555 0142
</div>
<div class="hero-box abs">
  <span class="dot"></span><span class="rule"></span>
  <div><h1>Vela Interiors</h1><p>Interior business &amp; new construction company</p></div>
</div>
<svg class="abs arrow" style="left:34px" width="26" height="32" viewBox="0 0 26 32"><path d="M20 3 7 16l13 13" fill="none" stroke="#111" stroke-width="6"/></svg>
<svg class="abs arrow" style="left:1138px" width="26" height="32" viewBox="0 0 26 32"><path d="M6 3l13 13L6 29" fill="none" stroke="#111" stroke-width="6"/></svg>

<section class="welcome abs">
  <h2>Welcome to Vela Interiors</h2>
  <p>Lorem Ipsum is simply dummy text of the printing and typesetting industry. Lorem Ipsum has been the industry's standard dummy text ever since the 1500s, when an unknown printer took a galley of type and scrambled it to make a type specimen book. It has survived not only five centuries, but also the leap into electronic typesetting, remaining essentially unchanged.</p>
  <a class="btn solid" href="#" style="left:423px;top:254px;width:170px;height:39px">About Vela Interiors</a>
  <a class="btn line" href="#" style="left:607px;top:254px;width:170px;height:39px">Contact Vela Interiors</a>
</section>

<section class="split abs" style="top:1009px">
  <div class="side"></div>
  <div class="card" style="left:86px;top:107px;width:262px;height:266px">
    <div class="photo" role="img" aria-label="Photo of a bedroom interior" style="inset:0;background:linear-gradient(160deg,#d8c8b0,#8a7360 70%,#5e4a3c)"></div>
    <div class="label">Interior Design</div>
  </div>
  <div class="card" style="left:362px;top:107px;width:262px;height:266px">
    <div class="photo" role="img" aria-label="Photo of a newly built house with pool" style="inset:0;background:linear-gradient(180deg,#7ea3c9,#c9b59a 50%,#2f5a6e)"></div>
    <div class="label">Construction</div>
  </div>
  <a class="btn solid" href="#" style="left:278px;top:388px;width:155px;height:39px">View More ›</a>
  <div class="photo" role="img" aria-label="Photo of a children's loft bed with stairs" style="left:645px;top:55px;width:389px;height:372px;background:linear-gradient(170deg,#cfc5b5,#8a7d6c 55%,#b59c7e)"></div>
  <div class="vtitle" style="left:1043px;top:122px">WHAT WE DO.</div>
</section>

<section class="feature abs" role="img" aria-label="Dim background photo of a staircase interior">
  <div class="vtitle" style="left:98px;top:92px;transform:rotate(180deg)">FEATURE SERVICES</div>
  <div class="card" style="left:172px;top:111px;width:299px;height:295px">
    <div class="photo" role="img" aria-label="Photo of a decorated living room" style="inset:0;background:linear-gradient(170deg,#e6e2da,#bdb5a8 60%,#7d6f60)"></div>
    <div class="label">Decorating</div>
  </div>
  <div class="card" style="left:494px;top:111px;width:300px;height:295px">
    <div class="photo" role="img" aria-label="Photo of a pink and white floral arrangement" style="inset:0;background:radial-gradient(circle at 50% 40%,#e9c3c0,#b78a7d 50%,#4b5a3b)"></div>
    <div class="label">Floral Arrangements</div>
  </div>
  <div class="card" style="left:815px;top:111px;width:299px;height:295px">
    <div class="photo" role="img" aria-label="Photo of a holiday ornament on a tree" style="inset:0;background:radial-gradient(circle at 55% 50%,#e89a3a,#7a3a14 40%,#1f2a14)"></div>
    <div class="label">Holiday Decorating</div>
  </div>
</section>

<section class="split abs" style="top:2006px">
  <div class="side"></div>
  <div class="card" style="left:86px;top:107px;width:262px;height:266px">
    <div class="photo" role="img" aria-label="Photo of an unfinished room before renovation" style="inset:0;background:linear-gradient(160deg,#b0a281,#7a6c52 60%,#4d4436)"></div>
    <div class="label">Before</div>
  </div>
  <div class="card" style="left:362px;top:107px;width:262px;height:266px">
    <div class="photo" role="img" aria-label="Photo of the finished room after renovation" style="inset:0;background:linear-gradient(160deg,#c9c7bf,#8f8d85 60%,#4e4a42)"></div>
    <div class="label">After</div>
  </div>
  <a class="btn solid" href="#" style="left:278px;top:387px;width:155px;height:39px">View More ›</a>
  <div class="photo" role="img" aria-label="Photo of a finished living room with beamed ceiling" style="left:645px;top:52px;width:389px;height:373px;background:linear-gradient(170deg,#5a4030,#9a7a5a 45%,#3a2c22)"></div>
  <div class="vtitle" style="left:1043px;top:100px">BEFORE &amp; AFTER</div>
</section>

<section class="touch abs" role="img" aria-label="Dark background photo of a furnished room">
  <h2>Get In Touch</h2>
  <div class="field abs">Enter your email...</div>
  <div class="send abs">SUBSCRIBE</div>
</section>

<footer class="footer abs">
  <div class="brand abs"><span class="dot"></span><span>Vela Interiors</span></div>
  <div class="socials abs"><i></i><i></i><i></i><i></i><i></i></div>
  <div class="col abs" style="left:392px;top:62px">
    <h4>Contact Info:</h4>
    <ul class="contact">
      <li><svg width="12" height="16" viewBox="0 0 12 16"><path fill="#111" d="M6 0a6 6 0 0 0-6 6c0 4.5 6 10 6 10s6-5.5 6-10a6 6 0 0 0-6-6zm0 8.5A2.5 2.5 0 1 1 6 3.5a2.5 2.5 0 0 1 0 5z"/></svg><span>Vela Interiors<br>48 Harbour View Road, Auckland, 1010.</span></li>
      <li><svg width="14" height="14" viewBox="0 0 24 24"><path fill="#111" d="M6.6 10.8a15 15 0 0 0 6.6 6.6l2.2-2.2c.3-.3.7-.4 1-.2 1.1.4 2.3.6 3.6.6.6 0 1 .4 1 1V20c0 .6-.4 1-1 1A17 17 0 0 1 3 4c0-.6.4-1 1-1h3.5c.6 0 1 .4 1 1 0 1.3.2 2.5.6 3.6.1.3 0 .7-.2 1z"/></svg><span>Tel: +0100 555 0142</span></li>
      <li><svg width="16" height="12" viewBox="0 0 16 12"><path fill="#111" d="M0 0h16v2L8 7 0 2zM0 4l8 5 8-5v8H0z"/></svg><span>Mail: hello@velainteriors.com</span></li>
    </ul>
  </div>
  <div class="col abs" style="left:764px;top:62px">
    <h4>Quick Links:</h4>
    <ul class="links"><li>Home</li><li>What We Do</li><li>Who We Are</li><li>Our Works</li><li>Blog</li><li>Contact us</li></ul>
  </div>
  <div class="col abs" style="left:949px;top:62px">
    <h4>Services:</h4>
    <ul class="links" style="line-height:25px"><li>Interior Design</li><li>New Construction</li><li>Decorating</li><li>Floral Arrangements</li><li>Holiday Decorating</li></ul>
  </div>
  <div class="rule abs"></div>
  <p class="copy abs">Copyright © 2018. Vela Interiors. All rights reserved.</p>
</footer>

</body>
</html>
```